Wordpress Powered Website. Outstanding Design Required. Using Morvenic Theme

Designers will not need to create anything other than the home page but there are some design elements on the home page which also need to be factored in: 6 product place holders and 2-3 slides for a slideshow (with images I provide).

Designers will need to familiarise themselves with the Morvenic theme to make sure that their design will work within the theme.

The winning designer will set up all the pages and navigation in place. This includes social media icons, favicon, widgets, etc. In other words, the home page needs to be designed and coded and the other preset theme pages need to be organised in a way that we can start using the website on completion of the job.

Most of the designs I had last time were too colourful. This needs to be subtle not in your face.

Background to the business/website:
Ridgeway Banners is a new Australian venture which will sell large format printed banners and other signage. The market is very competitive so it is important to stand out visually and to have a website which is clean, easy to navigate and easy to order. It will be a combination of online sales and assisted sales but all sales enquiries will come from the website.

As our business is focused on presentation it is vital to have excellent design.
Purchased theme is Morvenic. Only this theme is to be used.

1. A home page using all the preset features of the Morvenic theme - it will just be basically taking my wireframe and inputting it to the live theme.
2. A three slide slideshow, ideally with an edited video. The static image slides can be provided by me during the handover. Placeholder for now.
Similar to this one: http://thecedarhollow.example.au/

Attached is the logo which must be utilised, although it could also sit on a dark background. There is our mascot as well which can be used but does not have to be included.

Target Market(s)

Primarily B2B (business to business)
Main industries will be Construction, Retail, Community, Events & Trade Shows

Industry/Entity Type

Printing

Coding

Coded - Design and coding required

Font styles to use
Sans Serif

Requirements
Must have
• Must have the design files made to web pages within the Wordpress environment.
Nice to have
• Clean design. Stand out from competitors based on design.
Should not have
• Should not look like any competitor

```html
<!DOCTYPE html>
<html lang="en">
<head>
<meta charset="utf-8">
<title>Ridgeway Banners</title>
<link href="https://fonts.googleapis.com/css2?family=Lato:ital,wght@0,400;0,700;0,900;1,400;1,700;1,900&family=Oswald:wght@400;500&display=swap" rel="stylesheet">
<style>
:root{
  --ink:#222;
  --text:#444;
  --muted:#666;
  --red:#e41b17;
  --blue:#1a6fc4;
  --grey-bg:#f3f3f3;
  --dark:#111;
  --footer:#1b1b1b;
  --white:#fff;
}
*{box-sizing:border-box;margin:0;padding:0}
html,body{width:1200px;height:3377px;overflow:hidden}
body{position:relative;font-family:'Lato',sans-serif;color:var(--text);background:var(--white)}
.abs{position:absolute}
.topbar{top:0;left:0;width:1200px;height:36px;background:var(--dark);color:var(--white);font-size:14px;font-weight:700}
.social{display:flex;gap:9px;position:absolute;top:11px}
.social svg{display:block}
.topbar .contact{position:absolute;right:97px;top:9px;display:flex;gap:30px;align-items:center}
.topbar .contact div{display:flex;align-items:center;gap:8px}
.header{top:36px;left:0;width:1200px;height:83px;background:var(--white);border-bottom:1px solid #eee}
.brand{position:absolute;left:99px;top:24px;display:flex;align-items:center;gap:10px;font-weight:900;font-size:28px;color:var(--red);letter-spacing:.5px}
.brand i{width:26px;height:26px;background:var(--blue);display:block}
.nav{position:absolute;right:99px;top:34px;display:flex;font-size:12px;font-weight:700;letter-spacing:1px;color:var(--ink)}
.nav a{padding:0 34px;border-left:1px solid #ddd;color:inherit;text-decoration:none}
.nav a:first-child{border-left:0}
.hero{top:119px;left:0;width:1200px;height:428px;overflow:hidden;
  background:
   radial-gradient(ellipse 260px 200px at 200px 120px,rgba(88,150,190,.55),transparent 70%),
   radial-gradient(ellipse 300px 190px at 560px 110px,rgba(200,120,60,.55),transparent 70%),
   radial-gradient(ellipse 240px 180px at 900px 90px,rgba(190,80,60,.45),transparent 70%),
   linear-gradient(180deg,rgba(0,0,0,0) 55%,rgba(0,0,0,.35)),
   linear-gradient(90deg,#4b3f38,#6a5a4e 30%,#574a41 60%,#3b3632)}
.hero:before{content:"";position:absolute;inset:0;background:rgba(0,0,0,.28)}
.hero-text{position:absolute;top:168px;width:1200px;text-align:center;font-family:'Oswald',sans-serif;color:var(--white);font-size:31px;line-height:42px;text-shadow:0 1px 3px rgba(0,0,0,.5)}
.btn{display:inline-block;background:var(--red);color:var(--white);font-family:'Lato',sans-serif;font-weight:700;font-size:14px;padding:8px 16px}
.hero .btn{position:absolute;top:279px;left:523px}
.arrow{position:absolute;top:196px}
.sec-title{position:absolute;width:1200px;text-align:center;font-weight:900;font-size:24px;color:var(--ink);letter-spacing:.5px}
.sec-title:after{content:"";display:block;width:220px;height:1px;background:#ddd;margin:12px auto 0}
.tile{position:absolute;width:300px;height:205px;display:flex;align-items:center;justify-content:center;color:var(--white);font-weight:900;font-size:18px;letter-spacing:.5px;text-shadow:0 1px 4px rgba(0,0,0,.6);box-shadow:inset 0 0 0 2000px rgba(0,0,0,.22)}
.grey{left:0;width:1200px;background:var(--grey-bg)}
.feature{position:absolute;width:240px;text-align:center;top:1281px}
.feature .ico{width:112px;height:112px;border-radius:50%;background:var(--blue);margin:0 auto;display:flex;align-items:center;justify-content:center}
.feature h3{font-size:14px;font-weight:700;color:var(--ink);margin-top:22px;letter-spacing:.3px}
.feature p{font-size:12.5px;line-height:20px;color:var(--muted);margin-top:18px}
.step{position:absolute;top:1686px;width:240px;text-align:center}
.step .ring{width:136px;height:136px;border-radius:50%;border:5px solid var(--red);background:#3a3a3a;margin:0 auto;display:flex;align-items:center;justify-content:center;box-shadow:0 6px 10px rgba(0,0,0,.25)}
.step h4{font-size:13px;font-weight:700;color:var(--ink);margin-top:26px;letter-spacing:.5px}
.dots{position:absolute;top:1745px;display:flex;gap:16px;align-items:center}
.dots span{border-radius:50%;background:#ddd;display:block}
.gallery{top:2016px;left:0;width:1200px;height:414px;background:var(--white)}
.cell{position:absolute;box-shadow:inset 0 0 60px rgba(0,0,0,.18)}
.overlay{display:flex;align-items:center;justify-content:center;text-align:center;color:var(--white);font-weight:900;font-size:17px;line-height:22px;background:linear-gradient(rgba(40,40,40,.78),rgba(40,40,40,.78)),linear-gradient(135deg,#c0393b,#6b2a2c);box-shadow:none}
.about-body{top:2557px;left:99px;width:705px;font-size:13.5px;line-height:19.5px;color:var(--text)}
.about-body h3{font-size:15px;font-weight:900;color:var(--ink);margin-bottom:4px}
.about-body p{margin-bottom:12px}
.quote{top:2870px;left:0;width:1200px;height:277px;background:
  radial-gradient(ellipse 300px 200px at 250px 60px,rgba(255,255,255,.45),transparent 70%),
  radial-gradient(ellipse 320px 220px at 950px 200px,rgba(200,120,130,.5),transparent 70%),
  linear-gradient(100deg,#9e98b0,#e8dcd2 35%,#ecd6bf 60%,#d8a8a8 85%,#c99fb0)}
.quote h2{position:absolute;top:44px;width:1200px;text-align:center;color:var(--white);font-weight:700;font-size:24px;letter-spacing:1px}
.field{position:absolute;background:var(--white);font-size:11px;color:#555;padding:7px 10px;height:30px}
.quote .btn{position:absolute;top:201px;left:549px;width:99px;text-align:center;padding:6px 0;font-size:15px}
.support{top:3147px;left:0;width:1200px;height:163px;background:linear-gradient(180deg,#5ea833,#3f7f22)}
.support h2{position:absolute;top:28px;width:1200px;text-align:center;color:var(--white);font-style:italic;font-weight:900;font-size:26px}
.s-item{position:absolute;top:90px;display:flex;gap:14px;align-items:center;color:var(--white)}
.s-item b{display:block;font-style:italic;font-size:18px}
.s-item small{display:block;font-style:italic;font-size:13px;opacity:.85}
.footer{top:3310px;left:0;width:1200px;height:67px;background:var(--footer);color:var(--white);font-size:12px;font-weight:700;letter-spacing:.5px}
</style>
</head>
<body>

<div class="abs topbar">
  <div class="social" style="left:99px">
    <svg width="14" height="14" viewBox="0 0 14 14"><circle cx="3" cy="7" r="2" fill="#fff"/><circle cx="11" cy="3" r="2" fill="#fff"/><circle cx="11" cy="11" r="2" fill="#fff"/><path d="M3 7l8-4M3 7l8 4" stroke="#fff" stroke-width="1.3"/></svg>
    <svg width="14" height="14" viewBox="0 0 14 14"><path d="M1 2h12v8H6l-3 3v-3H1z" fill="#fff"/></svg>
    <svg width="14" height="14" viewBox="0 0 14 14"><rect x="1" y="3" width="12" height="9" fill="#fff"/><path d="M1 3l6 5 6-5" stroke="#111" stroke-width="1.2" fill="none"/></svg>
    <svg width="14" height="14" viewBox="0 0 14 14"><circle cx="2.5" cy="11.5" r="1.6" fill="#fff"/><path d="M1 6a7 7 0 017 7M1 1.5A11.5 11.5 0 0112.5 13" stroke="#fff" stroke-width="1.8" fill="none"/></svg>
    <svg width="14" height="14" viewBox="0 0 14 14"><path d="M6 8l2-2M5 6L3 8a2 2 0 003 3l2-2M9 8l2-2a2 2 0 00-3-3L6 5" stroke="#fff" stroke-width="1.6" fill="none"/></svg>
  </div>
  <div class="contact">
    <div><svg width="16" height="12" viewBox="0 0 16 12"><rect width="16" height="12" fill="#fff"/><path d="M0 0l8 7 8-7" stroke="#111" stroke-width="1.5" fill="none"/></svg>info@ridgewaybanners.example</div>
    <div><svg width="14" height="14" viewBox="0 0 24 24"><path fill="#fff" d="M6.6 10.8a15 15 0 006.6 6.6l2.2-2.2c.3-.3.7-.4 1-.2 1.1.4 2.3.6 3.6.6.6 0 1 .4 1 1V20c0 .6-.4 1-1 1A17 17 0 013 4c0-.6.4-1 1-1h3.5c.6 0 1 .4 1 1 0 1.3.2 2.5.6 3.6.1.3 0 .7-.2 1z"/></svg>123-456-7890</div>
  </div>
</div>

<header class="abs header">
  <div class="brand"><i></i>Ridgeway Banners</div>
  <nav class="nav"><a>PRODUCTS</a><a>GET A QUOTE</a><a>CONTACT US</a></nav>
</header>

<section class="abs hero" role="img" aria-label="Slideshow photo: printed banners displayed in a public hall">
  <svg class="arrow" style="left:80px" width="18" height="34" viewBox="0 0 18 34"><path d="M16 2L2 17l14 15" stroke="#fff" stroke-width="2" fill="none"/></svg>
  <svg class="arrow" style="right:80px" width="18" height="34" viewBox="0 0 18 34"><path d="M2 2l14 15L2 32" stroke="#fff" stroke-width="2" fill="none"/></svg>
  <div class="hero-text">We Are A New Australian Firm Which Will Sell<br>Large Format Printed Banners And Other Signage Material</div>
  <span class="btn">CONACT NOW !</span>
</section>

<h2 class="sec-title" style="top:588px">OUR PRODUCTS</h2>
<div class="tile" style="left:99px;top:660px;background:radial-gradient(circle at 30% 30%,#c98a3c,transparent 60%),linear-gradient(135deg,#8a5a2c,#4a2a14)" role="img" aria-label="Banners and fabrics photo">BANNERS &amp; FABRICS</div>
<div class="tile" style="left:449px;top:660px;background:radial-gradient(circle at 70% 40%,#d8d0cc,transparent 55%),linear-gradient(135deg,#c23a3a,#8a7a78 50%,#3a4a7a)" role="img" aria-label="Boards and signs photo">BOARDS &amp; SIGNS</div>
<div class="tile" style="left:799px;top:660px;background:radial-gradient(circle at 30% 40%,#d24a4a,transparent 45%),linear-gradient(180deg,#6f9ac0,#9ab8cc 55%,#c8a878)" role="img" aria-label="Flags on a beach photo">FLAGS &amp; POS</div>
<div class="tile" style="left:99px;top:903px;background:radial-gradient(circle at 30% 70%,#e08a2a,transparent 45%),linear-gradient(135deg,#8fae8a,#b8b06a 50%,#4a6a3a)" role="img" aria-label="Self adhesive vinyl print photo">SELF ADHESIVE VINYLS</div>
<div class="tile" style="left:449px;top:903px;background:radial-gradient(circle at 45% 50%,#c8c4c0,transparent 45%),linear-gradient(135deg,#6b6b6b,#2e2e2e)" role="img" aria-label="Pull up banners photo">PULL UP BANNERS</div>
<div class="tile" style="left:799px;top:903px;background:radial-gradient(circle at 45% 55%,#e6d8c8,transparent 45%),linear-gradient(135deg,#7a4a32,#3a2218)" role="img" aria-label="Posters on a table photo">POSTERS</div>

<section class="abs grey" style="top:1153px;height:407px"></section>
<h2 class="sec-title" style="top:1190px">OUR DIFFERENCE</h2>
<div class="feature" style="left:89px"><div class="ico"><svg width="50" height="50" viewBox="0 0 24 24"><circle cx="10" cy="10" r="6" stroke="#fff" stroke-width="2.5" fill="none"/><path d="M14.5 14.5L21 21" stroke="#fff" stroke-width="3"/></svg></div><h3>Attention To Detail</h3><p>Lorem ipsum dolor sit amet,<br>consectetur adipiscing elit. Aenean et<br>dignissim sem, interdum risus.</p></div>
<div class="feature" style="left:351px"><div class="ico"><svg width="50" height="50" viewBox="0 0 24 24"><circle cx="12" cy="12" r="8" stroke="#fff" stroke-width="2" fill="none"/><circle cx="12" cy="12" r="3" fill="#fff"/><path d="M12 1v5M12 18v5M1 12h5M18 12h5" stroke="#fff" stroke-width="2"/></svg></div><h3>FAST AND FLEXIBLE</h3><p>Lorem ipsum dolor sit amet,<br>consectetur adipiscing elit. Aenean et<br>dignissim sem, interdum risus.</p></div>
<div class="feature" style="left:607px"><div class="ico"><svg width="50" height="50" viewBox="0 0 24 24"><path fill="#fff" d="M2 10h4v11H2zM8 21V10l5-8c1.5 0 2.5 1 2 3l-1 4h6c1.2 0 2 1 1.8 2.2l-1.6 8A2 2 0 0118.2 21z"/></svg></div><h3>SECURE DELIVERY</h3><p>Lorem ipsum dolor sit amet,<br>consectetur adipiscing elit. Aenean et<br>dignissim sem, interdum risus.</p></div>
<div class="feature" style="left:866px"><div class="ico"><svg width="50" height="50" viewBox="0 0 24 24"><rect x="5" y="8" width="14" height="14" rx="2" fill="#fff"/><path d="M9 8V5a3 3 0 016 0v3" stroke="#fff" stroke-width="2" fill="none"/><text x="12" y="19" text-anchor="middle" font-size="9" font-weight="700" fill="#1a6fc4" font-family="Lato,sans-serif">$</text></svg></div><h3>NICE PRICES</h3><p>Lorem ipsum dolor sit amet,<br>consectetur adipiscing elit. Aenean et<br>dignissim sem, interdum risus.</p></div>

<h2 class="sec-title" style="top:1604px">OUR PROCESS</h2>
<div class="step" style="left:166px"><div class="ring"><svg width="46" height="46" viewBox="0 0 24 24"><path d="M3 5h10v3M3 5v14h10v-3" stroke="#fff" stroke-width="2" fill="none"/><path d="M9 12h12M17 8l4 4-4 4" stroke="#fff" stroke-width="2" fill="none"/></svg></div><h4>LOREM IPSUM SIT DOLOR</h4></div>
<div class="step" style="left:481px"><div class="ring"><svg width="46" height="46" viewBox="0 0 24 24"><rect x="5" y="4" width="14" height="18" rx="1" stroke="#fff" stroke-width="2" fill="none"/><rect x="9" y="2" width="6" height="4" fill="#fff"/><path d="M8 10h8M8 14h8M8 18h5" stroke="#fff" stroke-width="2"/></svg></div><h4>LOREM IPSUM SIT DOLOR</h4></div>
<div class="step" style="left:792px"><div class="ring"><svg width="46" height="46" viewBox="0 0 24 24"><path d="M4 4h10v4M4 4v16h12v-3" stroke="#fff" stroke-width="2" fill="none"/><path d="M10 13h11M17 9l4 4-4 4" stroke="#fff" stroke-width="2" fill="none"/></svg></div><h4>LOREM IPSUM SIT DOLOR</h4></div>
<div class="dots" style="left:387px"><span style="width:9px;height:9px"></span><span style="width:13px;height:13px"></span><span style="width:18px;height:18px"></span><span style="width:24px;height:24px"></span></div>
<div class="dots" style="left:703px"><span style="width:9px;height:9px"></span><span style="width:13px;height:13px"></span><span style="width:18px;height:18px"></span><span style="width:24px;height:24px"></span></div>

<section class="abs grey" style="top:1902px;height:114px"></section>
<h2 class="sec-title" style="top:1941px">OUR LATEST WORK</h2>

<section class="abs gallery">
  <div class="cell" style="left:0;top:0;width:194px;height:115px;background:linear-gradient(135deg,#d4a060,#8a6a4a)" role="img" aria-label="Printed fabric banners photo"></div>
  <div class="cell" style="left:0;top:117px;width:194px;height:174px;background:radial-gradient(circle at 40% 50%,#f0e24a,transparent 60%),linear-gradient(135deg,#d8c63a,#3a3a3a)" role="img" aria-label="Colourful posters photo"></div>
  <div class="cell" style="left:0;top:293px;width:194px;height:121px;background:linear-gradient(135deg,#b6c23c,#e0d84a 50%,#6a8a3a)" role="img" aria-label="Pull up banner row photo"></div>
  <div class="cell" style="left:196px;top:0;width:193px;height:142px;background:linear-gradient(135deg,#c8d4e0,#5a7aa4)" role="img" aria-label="Desk with print proofs photo"></div>
  <div class="cell" style="left:196px;top:144px;width:193px;height:270px;background:radial-gradient(circle at 50% 40%,#e8c0a0,transparent 55%),linear-gradient(135deg,#a8785a,#4a3a3a)" role="img" aria-label="Event banner with crowd photo"></div>
  <div class="cell" style="left:391px;top:0;width:194px;height:282px;background:linear-gradient(90deg,#9a98a8,#e0dcd8 30%,#6a5a7a 55%,#d8d4d0 80%,#8a8498)" role="img" aria-label="Display stand banners photo"></div>
  <div class="cell" style="left:391px;top:284px;width:194px;height:130px;background:linear-gradient(135deg,#4a6a80,#2e4658)" role="img" aria-label="Printed icon panels photo"></div>
  <div class="cell" style="left:587px;top:0;width:216px;height:124px;background:linear-gradient(135deg,#9a8a86,#5a4a48)" role="img" aria-label="Printed brochures photo"></div>
  <div class="cell overlay" style="left:587px;top:126px;width:216px;height:288px">LOREM IPSUM<br>DOLOR SIT AMET</div>
  <div class="cell" style="left:805px;top:0;width:196px;height:205px;background:radial-gradient(circle at 55% 65%,#d43a34,transparent 50%),linear-gradient(180deg,#f2efea,#e4e0da)" role="img" aria-label="Typographic poster photo"></div>
  <div class="cell" style="left:805px;top:207px;width:196px;height:207px;background:linear-gradient(160deg,#e8b84a,#d85a3a 45%,#4a6ab0)" role="img" aria-label="Row of flags photo"></div>
  <div class="cell" style="left:1003px;top:0;width:197px;height:115px;background:linear-gradient(180deg,#9ab0bc,#2a3438)" role="img" aria-label="Corflute signs photo"></div>
  <div class="cell" style="left:1003px;top:117px;width:197px;height:174px;background:radial-gradient(circle at 40% 50%,#e84a44,transparent 55%),linear-gradient(135deg,#f0ecea,#c8c4c0)" role="img" aria-label="Sale signs photo"></div>
  <div class="cell" style="left:1003px;top:293px;width:197px;height:121px;background:linear-gradient(135deg,#4aa88e,#e8ece8 60%,#3a8a72)" role="img" aria-label="Printed flyers photo"></div>
</section>

<h2 class="sec-title" style="top:2478px">ABOUT RIDGEWAY BANNERS</h2>
<div class="abs about-body">
  <h3>OUR LITTLE BUSINESS</h3>
  <p>Lorem ipsum dolor sit amet, consectetur adipiscing elit. Aenean et dignissim sem, interdum risus. Vestibulum consectetur nisi mollis diam pulvinar adipiscing. Vestibulum ut urna nec nibh adipiscing facilisis. Etiam auctor porta lacus ac luctus. Praesent ac libero fermentum, rhoncus magna a, dapibus mauris. Nam ut auctor justo. Sed ante odio, luctus quis nequ nec, adipiscing eleifend arcu. Integer nunc turpis, porttitor at lorem ut.Quisque hendrerit Lorem ipsum dolor sit amet, consectetur adipiscing elit. Aenean et dignissim sem, interdum risus. Vestibulum consectetur nisi mollis diam pulvinar adipiscing. Vestibulum ut urna nec nibh adipiscing facilisis. Etiam auctor porta lacus ac luctus. Praesent ac libero fermentum, rhoncus magna a, dapibus mauris.</p>
  <p>Lorem ipsum dolor sit amet, consectetur adipiscing elit. Aenean et dignissim sem, interdum risus. Vestibulum consectetur nisi mollis diam pulvinar adipiscing. Vestibulum ut urna nec nibh adipiscing facilisis. Etiam auctor porta lacus ac luctus. Praesent ac libero fermentum, rhoncus magna a, dapibus mauris.</p>
</div>
<div class="abs" style="left:837px;top:2560px;width:262px;height:130px;background:radial-gradient(circle at 65% 45%,#4a5a9a,transparent 40%),linear-gradient(135deg,#e6ebf0,#a8b6c4)" role="img" aria-label="Photo of a staff member working at a print station"></div>
<div class="abs" style="left:837px;top:2706px;width:262px;height:128px;background:linear-gradient(180deg,#e4e6e8 0 35%,#2e323a 75%,#1e2228)" role="img" aria-label="Photo of the business team"></div>

<section class="abs quote">
  <h2>GET A QUOTE</h2>
  <div class="field" style="left:169px;top:115px;width:216px">Name</div>
  <div class="field" style="left:399px;top:115px;width:213px">Email</div>
  <div class="field" style="left:630px;top:115px;width:399px;height:68px">Your Message</div>
  <div class="field" style="left:169px;top:154px;width:216px">Phone Number</div>
  <div class="field" style="left:399px;top:154px;width:213px">Enquiry Type<svg style="position:absolute;right:10px;top:12px" width="9" height="6" viewBox="0 0 9 6"><path d="M0 0h9L4.5 6z" fill="#777"/></svg></div>
  <span class="btn">SUBMIT</span>
</section>

<section class="abs support">
  <h2>We're Dedicated to Our Customers 24x7</h2>
  <div class="s-item" style="left:99px"><svg width="34" height="34" viewBox="0 0 24 24"><path fill="#fff" d="M6.6 10.8a15 15 0 006.6 6.6l2.2-2.2c.3-.3.7-.4 1-.2 1.1.4 2.3.6 3.6.6.6 0 1 .4 1 1V20c0 .6-.4 1-1 1A17 17 0 013 4c0-.6.4-1 1-1h3.5c.6 0 1 .4 1 1 0 1.3.2 2.5.6 3.6.1.3 0 .7-.2 1z"/></svg><div><b>123-456-7890</b><small>Available 24/7 - Call us any time.</small></div></div>
  <div class="s-item" style="left:417px"><svg width="44" height="32" viewBox="0 0 44 32"><rect x="2" y="2" width="40" height="28" fill="none" stroke="#fff" stroke-width="3"/><path d="M2 2l20 16L42 2" stroke="#fff" stroke-width="3" fill="none"/></svg><div><b>Email Us</b><small>Have a question? Let us help.</small></div></div>
  <div class="s-item" style="left:724px"><svg width="44" height="34" viewBox="0 0 44 34"><ellipse cx="18" cy="13" rx="16" ry="11" fill="none" stroke="#fff" stroke-width="3"/><path d="M8 22l-4 8 10-5" fill="#fff"/><path d="M36 12c5 2 7 6 5 10l2 8-8-4" fill="none" stroke="#fff" stroke-width="3"/></svg><div><b>Live Chat</b><small>Online Support</small></div></div>
  <div class="s-item" style="left:930px"><span style="font-size:42px;font-weight:900">?</span><div><b>Help</b><small>Find your answers.</small></div></div>
</section>

<footer class="abs footer">
  <div style="position:absolute;left:99px;top:27px">PRODUCTS &nbsp;/&nbsp; GET A QUOTE &nbsp;/&nbsp; CONTACT US</div>
  <div class="social" style="left:545px;top:26px">
    <svg width="14" height="14" viewBox="0 0 14 14"><circle cx="3" cy="7" r="2" fill="#fff"/><circle cx="11" cy="3" r="2" fill="#fff"/><circle cx="11" cy="11" r="2" fill="#fff"/><path d="M3 7l8-4M3 7l8 4" stroke="#fff" stroke-width="1.3"/></svg>
    <svg width="14" height="14" viewBox="0 0 14 14"><path d="M1 2h12v8H6l-3 3v-3H1z" fill="#fff"/></svg>
    <svg width="14" height="14" viewBox="0 0 14 14"><rect x="1" y="3" width="12" height="9" fill="#fff"/><path d="M1 3l6 5 6-5" stroke="#1b1b1b" stroke-width="1.2" fill="none"/></svg>
    <svg width="14" height="14" viewBox="0 0 14 14"><circle cx="2.5" cy="11.5" r="1.6" fill="#fff"/><path d="M1 6a7 7 0 017 7M1 1.5A11.5 11.5 0 0112.5 13" stroke="#fff" stroke-width="1.8" fill="none"/></svg>
    <svg width="14" height="14" viewBox="0 0 14 14"><path d="M6 8l2-2M5 6L3 8a2 2 0 003 3l2-2M9 8l2-2a2 2 0 00-3-3L6 5" stroke="#fff" stroke-width="1.6" fill="none"/></svg>
  </div>
  <div style="position:absolute;right:99px;top:27px;font-size:11px">© 2016 RIDGEWAY BANNERS. ALL RIGHTS RESERVED.</div>
</footer>

</body>
</html>
```